wordpress website Carla Winfield, Author, Speaker and Coach

Need a wordpress blogging website for author/speaker/coach.
I have paid for hosting on nestparrot.
I am currently writing a book - Launchpad to Campus - Steps and strategies to prepare you to thrive in college and beyond. Eventually, I will have an Academic/Life Coaching program targeting high school and college students. This website's purpose is to build my email list. I can offer the following reports as incentive for email sign-up:
1. Six Habits That Get Your Teen Through University On Schedule and Debt-Light
2. Surprising Routes to Fund Your Degree
3. SAT/ACT vocabulary word of the day

facebook page: https://www.facebook.com/Carla-Winfield-AcademicLife-Coach-918273645501928/

I would like to have these pages:

1. Home or About page

High school is becoming more and more stressful for students. Not only are they taking more AP classes than ever before, and often spending $1,000’s on SAT/ACT prep programs, most are NOT prepared for success in college. Only 19% of students are graduating from college within 4 years and only 56% are graduating within 6 years. With the cost of higher education skyrocketing, each extra year of school can costs families $40,000 - $60,000 when you factor in living expenses. Then, when students do graduate, they are often underemployed.

Carla's approach is whole person oriented. Her programs help students learn life skills in addition to the study, time management skills, etc. offered by most academic coaching programs. Our program addresses all of the major causes of failure to graduate within 4 years, and is based on sound educational research. Carla's program initially provides the daily interaction needed to successfully change behaviors and seat new success habits, unlike many programs in which students interact with coaches only once a week.
Bio
Carla Winfield is a certified teacher and holds advanced certification in academic coaching and tutoring. She also is a certified trainer in the Morris Tellwright Achievement Keys. She has three successful adult children, and helped them overcome learning differences and thrive.

2. Blog

3. Contact - Include form (I split time between USA and Saudi Arabia, so I will call or email people back, but don't want to leave a phone number)
info@carlawinfield.example

4. Store – 1 book for now
Launchpad to Campus
Steps and strategies to prepare you to thrive in college and beyond
Available 12/01/2017
I could make a preview chapter available for download

5. Speaking
Carla Winfield is available for keynote addresses and half-day, full day or multi-day workshops. I will develop details later

6.Coaching programs
I will develop details later

Target Market(s)

high school students who are college bound and their parents

Number of Pages Required

5+ page

Font styles to use
Sans Serif

Colors

Designer to choose colors to be used in the design.

Requirements
Nice to have
• integration with post finch for contact management

```html
<!DOCTYPE html>
<html lang="en">
<head>
<meta charset="utf-8">
<title>Carla Winfield — Author, Speaker and Coach</title>
<link rel="stylesheet" href="https://fonts.googleapis.com/css2?family=Mulish:wght@400;600;700&family=Open+Sans:wght@400;600&display=swap">
<style>
:root{
  --green:#2f9a4a;
  --green-dark:#0f6f36;
  --green-lime:#58c23f;
  --purple:#7b80c6;
  --purple-light:#9ea3dc;
  --ink:#2f2f2f;
  --muted:#8a8a8a;
  --line:#d9d9d9;
  --soft:#f4f4f4;
  --white:#ffffff;
}
*{box-sizing:border-box;margin:0;padding:0}
html,body{width:1200px;height:3005px;overflow:hidden;background:var(--white)}
body{font-family:"Open Sans",Arial,sans-serif;color:var(--ink);position:relative}
a{text-decoration:none;color:inherit}
.abs{position:absolute}

/* header */
.site-header{position:absolute;left:0;top:0;width:1200px;height:110px;background:var(--white)}
.brand{position:absolute;left:128px;top:26px;display:flex;align-items:center;gap:14px}
.brand-dot{width:44px;height:44px;border-radius:50%;background:var(--green)}
.brand-name{font-family:"Mulish",Arial,sans-serif;font-weight:600;font-size:34px;color:var(--green-dark)}
.main-nav{position:absolute;top:44px;left:468px;display:flex;gap:0;font-family:"Mulish",Arial,sans-serif;font-size:18px;color:#7d7d7d}
.main-nav a{position:absolute;white-space:nowrap}
.main-nav .active{color:var(--green-dark);font-weight:700}

/* hero */
.hero{position:absolute;left:0;top:110px;width:1200px;height:550px;overflow:hidden}
.hero-photo{position:absolute;inset:0;background:
  radial-gradient(ellipse at 30% 70%,rgba(150,110,40,.55),transparent 45%),
  linear-gradient(180deg,#8f9c8a 0%,#b7b8a8 30%,#8e9c93 55%,#6f7f78 75%,#3e4a3c 100%)}
.hero-title{position:absolute;left:0;width:1200px;top:180px;text-align:center;font-family:"Mulish",Arial,sans-serif;font-weight:600;font-size:38px;line-height:44px;color:var(--white)}
.btn-outline{position:absolute;display:flex;align-items:center;justify-content:center;font-family:"Mulish",Arial,sans-serif;font-size:14px;letter-spacing:.5px;text-transform:uppercase}
.hero .btn-outline{left:526px;top:284px;width:142px;height:42px;border:2px solid var(--white);color:var(--white)}
.slider-dots{position:absolute;left:560px;top:474px;display:flex;gap:6px}
.slider-dots span{width:28px;height:4px;background:rgba(255,255,255,.7)}
.slider-dots span:first-child{background:var(--white)}
.hero-wave{position:absolute;left:0;bottom:0}

/* about */
.about-photo{position:absolute;left:156px;top:690px;width:340px;height:340px;border-radius:50%;background:radial-gradient(circle at 50% 40%,#d9a98e 0%,#b57d62 30%,#5a4438 60%,#1f1b1a 85%)}
.section-title{font-family:"Mulish",Arial,sans-serif;font-weight:400;font-size:36px;color:var(--ink)}
.about-title{position:absolute;left:534px;top:722px}
.about-text{position:absolute;left:534px;top:780px;width:490px;font-size:13.5px;line-height:22px;color:var(--muted)}
.about .btn-outline{left:534px;top:960px;width:144px;height:42px;border:2px solid #555;color:#444}

/* coaching */
.coaching{position:absolute;left:0;top:1074px;width:1200px;height:442px;background:linear-gradient(100deg,#0f7336 0%,#1c8c42 45%,#3aa84a 100%);overflow:hidden}
.coaching-photo{position:absolute;left:0;top:0;width:1200px;height:442px;clip-path:polygon(710px 0,1200px 0,1200px 442px,535px 442px);background:radial-gradient(circle at 72% 48%,#f1f4ea 0%,#cfe1b8 14%,#8cc45c 32%,#4ea83c 60%,#2d8e34 100%)}
.coaching-title{position:absolute;left:132px;top:82px;font-family:"Mulish",Arial,sans-serif;font-size:32px;color:var(--white)}
.coaching-text{position:absolute;left:132px;top:136px;width:480px;font-size:13.5px;line-height:22px;color:var(--white)}
.coaching .btn-outline{left:134px;top:302px;width:144px;height:42px;border:2px solid var(--white);color:var(--white)}

/* blogs */
.blogs{position:absolute;left:0;top:1516px;width:1200px;height:520px;background:var(--soft)}
.blogs-title{position:absolute;left:0;width:1200px;top:34px;text-align:center;font-family:"Mulish",Arial,sans-serif;font-size:32px;color:var(--green)}
.blog-card{position:absolute;top:98px;width:300px;text-align:center}
.blog-image{width:300px;height:222px}
.blog-card:nth-of-type(1) .blog-image{background:linear-gradient(160deg,#e9e7b3 0%,#b8d07a 45%,#6aa33b 100%)}
.blog-card:nth-of-type(2) .blog-image{background:linear-gradient(180deg,#e08a3a 0%,#b5541f 45%,#5a2a14 100%)}
.blog-card:nth-of-type(3) .blog-image{background:linear-gradient(180deg,#f6c543 0%,#ee9a2a 50%,#8a4a1c 100%)}
.blog-title{margin-top:18px;font-family:"Mulish",Arial,sans-serif;font-size:23px;color:var(--ink)}
.blog-excerpt{margin:10px auto 0;width:270px;font-size:11.5px;line-height:17px;color:var(--muted)}
.blog-more{display:block;margin-top:10px;font-family:"Mulish",Arial,sans-serif;font-size:13px;font-weight:600;color:var(--green-lime)}

/* features */
.feature-box{position:absolute;top:2118px;width:462px;height:242px;border:2px solid;text-align:center;background:var(--white)}
.feature-book{left:124px;border-color:var(--purple)}
.feature-speaking{left:606px;border-color:var(--green)}
.feature-icon{position:absolute;left:181px;top:-52px;width:100px;height:100px;border-radius:50%;background:var(--white);border:2px solid;display:flex;align-items:center;justify-content:center}
.feature-book .feature-icon{border-color:var(--purple)}
.feature-speaking .feature-icon{border-color:var(--green)}
.feature-kicker{margin-top:68px;font-family:"Mulish",Arial,sans-serif;font-size:19px;color:var(--purple)}
.feature-title{font-family:"Mulish",Arial,sans-serif;font-size:25px;color:var(--purple)}
.feature-speaking .feature-title{margin-top:74px;font-weight:600;color:var(--green)}
.feature-text{margin:14px auto 0;width:340px;font-size:12.5px;line-height:21px;color:var(--muted)}
.feature-speaking .feature-text{width:400px;font-size:11.5px;margin-top:14px}
.hex-btn{position:absolute;top:222px;height:38px;display:flex;align-items:center;justify-content:center;font-family:"Mulish",Arial,sans-serif;font-size:15px;color:var(--white);clip-path:polygon(14px 0,calc(100% - 14px) 0,100% 50%,calc(100% - 14px) 100%,14px 100%,0 50%)}
.feature-book .hex-btn{left:136px;width:182px;background:var(--purple)}
.feature-speaking .hex-btn{left:158px;width:156px;background:var(--green-lime)}

/* signup */
.signup{position:absolute;left:0;top:2452px;width:1200px;height:392px;background:linear-gradient(180deg,#8f94d4 0%,#a7abdf 55%,#c7c4e2 100%)}
.signup-title{position:absolute;left:150px;top:80px;font-family:"Mulish",Arial,sans-serif;font-size:27px;color:var(--white)}
.report-list{position:absolute;left:150px;top:144px;list-style:none;font-size:16px;line-height:33px;color:#f2f0e2}
.report-list li::before{content:"";display:inline-block;width:0;height:0;border-left:6px solid #f2f0e2;border-top:5px solid transparent;border-bottom:5px solid transparent;margin-right:9px}
.signup-form{position:absolute;left:150px;top:264px;display:flex;gap:12px}
.field{height:44px;background:var(--white);font-size:14px;color:#999;padding:0 12px;display:flex;align-items:center}
.field-name{width:270px}
.field-email{width:268px}
.subscribe{width:144px;height:44px;border:2px solid var(--white);color:var(--white);font-family:"Mulish",Arial,sans-serif;font-size:15px;display:flex;align-items:center;justify-content:center;margin-left:-6px}

/* footer */
.site-footer{position:absolute;left:0;top:2844px;width:1200px;height:161px;background:var(--white)}
.cert-badge{position:absolute;left:144px;top:20px;width:108px;height:108px;border-radius:50%;background:radial-gradient(circle at 40% 35%,#eeeeee,#a9a9a9 70%,#8a8a8a)}
.footer-nav{position:absolute;left:284px;top:44px;display:flex;gap:22px;font-family:"Mulish",Arial,sans-serif;font-size:14px;font-weight:600;color:var(--ink)}
.copyright{position:absolute;left:288px;top:80px;font-size:13px;color:#a5a5a5}
.social{position:absolute;left:920px;top:38px;display:flex;gap:6px}
.social span{width:34px;height:34px;border:2px solid var(--green-lime);display:flex;align-items:center;justify-content:center}
.social span i{width:8px;height:8px;background:var(--green-lime);border-radius:50%}
</style>
</head>
<body>

<header class="site-header">
  <a class="brand" href="#"><span class="brand-dot"></span><span class="brand-name">Carla Winfield</span></a>
  <nav class="main-nav">
    <a class="active" style="left:0">Home</a>
    <a style="left:82px">Blog</a>
    <a style="left:152px">Store</a>
    <a style="left:228px">Speaking</a>
    <a style="left:340px">Coaching Program</a>
    <a style="left:532px">Contact</a>
  </nav>
</header>

<section class="hero">
  <div class="hero-photo" role="img" aria-label="Photo of a woman sitting on a wooden jetty by a forest lake"></div>
  <h1 class="hero-title">Morbi diam mauris viverra in gravida<br>Aattis in ante morbi eget</h1>
  <a class="btn-outline" href="#">Read more</a>
  <div class="slider-dots"><span></span><span></span><span></span></div>
  <svg class="hero-wave" width="1200" height="140" viewBox="0 0 1200 140">
    <path d="M0 95 C 220 150, 520 140, 760 80 C 920 42, 1080 20, 1200 28 L1200 140 L0 140 Z" fill="#ffffff"/>
  </svg>
</section>

<section class="about">
  <div class="about-photo" role="img" aria-label="Portrait photo of Carla Winfield"></div>
  <h2 class="section-title about-title">About Me</h2>
  <p class="about-text">High school is becoming more and more stressful for students. Not only are they taking more AP classes than ever before, and often spending $1,000’s on SAT/ACT prep programs, most are NOT prepared for success in college. Only 19% of students are graduating from college within 4 years and only 56% are graduating within 6 years. With the cost of higher education skyrocketing, each extra year of school can costs families $40,000 - $60,000 when you factor in living expenses.</p>
  <a class="btn-outline" href="#">Read more</a>
</section>

<section class="coaching">
  <div class="coaching-photo" role="img" aria-label="Photo of a dandelion seed head with seeds blowing away"></div>
  <h2 class="coaching-title">Coaching Program</h2>
  <p class="coaching-text">Carla's approach is whole person oriented. Her programs help students learn life skills in addition to the study, time management skills, etc. offered by most academic coaching programs. Our program addresses all of the major causes of failure to graduate within 4 years, and is based on sound educational research. Carla's program initially provides the dailyinteraction needed to successfully change behaviors</p>
  <a class="btn-outline" href="#">Read more</a>
</section>

<section class="blogs">
  <h2 class="blogs-title">Latest Blogs</h2>
  <article class="blog-card" style="left:120px">
    <div class="blog-image" role="img" aria-label="Photo of a young woman enjoying the sun in a meadow"></div>
    <h3 class="blog-title">Your Blog Tittle here</h3>
    <p class="blog-excerpt">sociosqu ad litora torquent per conubia nostra per inceptos hymenaeos Proin nulla arcu nonummy luctus dictum eget</p>
    <a class="blog-more" href="#">READ MORE</a>
  </article>
  <article class="blog-card" style="left:448px">
    <div class="blog-image" role="img" aria-label="Photo of a person meditating at sunset"></div>
    <h3 class="blog-title">Your Blog Tittle here</h3>
    <p class="blog-excerpt">sociosqu ad litora torquent per conubia nostra per inceptos hymenaeos Proin nulla arcu nonummy luctus dictum eget</p>
    <a class="blog-more" href="#">READ MORE</a>
  </article>
  <article class="blog-card" style="left:774px">
    <div class="blog-image" role="img" aria-label="Photo of a woman raising her arms at sunrise"></div>
    <h3 class="blog-title">Your Blog Tittle here</h3>
    <p class="blog-excerpt">sociosqu ad litora torquent per conubia nostra per inceptos hymenaeos Proin nulla arcu nonummy luctus dictum eget</p>
    <a class="blog-more" href="#">READ MORE</a>
  </article>
</section>

<div class="feature-box feature-book">
  <div class="feature-icon">
    <svg width="52" height="40" viewBox="0 0 52 40" fill="none" stroke="#7b80c6" stroke-width="2.5" stroke-linejoin="round">
      <path d="M26 8 C 19 3, 10 3, 3 5 L3 35 C 10 33, 19 33, 26 37 C 33 33, 42 33, 49 35 L49 5 C 42 3, 33 3, 26 8 Z"/>
      <path d="M26 8 L26 37"/>
    </svg>
  </div>
  <p class="feature-kicker">My Book</p>
  <h3 class="feature-title">Launchpad to Campus</h3>
  <p class="feature-text">Steps and strategies to prepare you to thrive in college and beyond</p>
  <a class="hex-btn" href="#">READ MORE</a>
</div>

<div class="feature-box feature-speaking">
  <div class="feature-icon">
    <svg width="52" height="44" viewBox="0 0 52 44" fill="none" stroke="#2f9a4a" stroke-width="2.5" stroke-linejoin="round">
      <path d="M4 16 L14 16 L36 4 L36 36 L14 26 L4 26 Z"/>
      <path d="M12 26 L16 40 L22 40 L19 27"/>
      <path d="M42 14 C 46 17, 46 25, 42 28"/>
    </svg>
  </div>
  <h3 class="feature-title">Speaking</h3>
  <p class="feature-text">Praesent elementum elit ut tellus nec ultricies sit amet porttitor mattis enim in mosso libero interdum nec interdum vel blandit sed nulla in ullamcorper est eget tempor cursus neque mi</p>
  <a class="hex-btn" href="#">READ MORE</a>
</div>

<section class="signup" role="img" aria-label="Soft purple photo of friends jumping in a field at dusk">
  <h2 class="signup-title">Offer the following reports as incentive for email sign-up</h2>
  <ul class="report-list">
    <li>Six Habits That Get Your Teen Through University On Schedule and Debt-Light</li>
    <li>Surprising Routes to Fund Your Degree</li>
    <li>SAT/ACT vocabulary word of the day</li>
  </ul>
  <div class="signup-form">
    <span class="field field-name">Your Name</span>
    <span class="field field-email">Email address</span>
    <span class="subscribe">SUBSCRIBE</span>
  </div>
</section>

<footer class="site-footer">
  <div class="cert-badge" role="img" aria-label="Certified trainer badge"></div>
  <nav class="footer-nav">
    <a>Home</a><a>Blog</a><a>Store</a><a>Speaking</a><a>Coaching Program</a><a>Contact</a>
  </nav>
  <p class="copyright">© 2017 Company Name &nbsp;All right reserved</p>
  <div class="social" aria-label="Social links">
    <span><i></i></span><span><i></i></span><span><i></i></span><span><i></i></span>
  </div>
</footer>

</body>
</html>
```